Business card design for Keldra Engineering Tandem

We need a new business card design along with all the necessary to place an order. The company is Keldra Engineering Tandem and we recently updated our logo.

```html
<!DOCTYPE html>
<html lang="en">
<head>
<meta charset="utf-8">
<title>Keldra Engineering Tandem – Business Card</title>
<link rel="stylesheet" href="https://fonts.googleapis.com/css2?family=Montserrat:wght@400;500;700&display=swap">
<style>
  :root {
    --backdrop: #3b3c3e;
    --card: #ffffff;
    --gold: #e0bd22;
    --grey: #8f8f8e;
    --ink: #2b2b2b;
  }
  * { margin: 0; padding: 0; box-sizing: border-box; }
  html, body { width: 1200px; height: 1059px; overflow: hidden; }
  body {
    background: var(--backdrop);
    font-family: "Montserrat", Arial, sans-serif;
    position: relative;
  }
  .card {
    position: absolute;
    background: var(--card);
    border-radius: 28px;
  }
  .card--front { left: 256px; top: 100px; width: 688px; height: 393px; }
  .card--back  { left: 253px; top: 536px; width: 695px; height: 397px; }

  .wordmark {
    position: absolute;
    display: flex;
    align-items: center;
    color: var(--grey);
    font-weight: 500;
    white-space: nowrap;
  }
  .wordmark__square { background: var(--gold); flex: none; }
  .card--front .wordmark { left: 58px; top: 181px; font-size: 19px; gap: 10px; }
  .card--front .wordmark__square { width: 20px; height: 20px; }
  .card--back .wordmark { left: 0; right: 0; top: 174px; justify-content: center; font-size: 38px; gap: 18px; }
  .card--back .wordmark__square { width: 40px; height: 40px; }

  .divider {
    position: absolute;
    left: 366px; top: 90px;
    width: 2px; height: 213px;
    background: var(--gold);
  }
  .details { position: absolute; left: 394px; top: 84px; color: var(--ink); }
  .details__name { color: var(--gold); font-weight: 700; font-size: 29px; letter-spacing: 0.3px; line-height: 34px; }
  .details__role { font-size: 18px; line-height: 24px; }
  .details__address { font-size: 18px; line-height: 28px; margin-top: 14px; }
  .details__contacts { list-style: none; margin-top: 12px; }
  .details__contacts li { display: flex; align-items: center; gap: 8px; font-size: 18px; line-height: 27.5px; }
  .details__contacts svg { width: 15px; height: 15px; fill: var(--gold); flex: none; }
</style>
</head>
<body>
  <section class="card card--front">
    <div class="wordmark">
      <span class="wordmark__square"></span>
      <span class="wordmark__name">Keldra Engineering Tandem</span>
    </div>
    <div class="divider"></div>
    <div class="details">
      <h1 class="details__name">MARCUS HALE</h1>
      <p class="details__role">Managing Director</p>
      <p class="details__address">Your address, City<br>State, Zip 1234</p>
      <ul class="details__contacts">
        <li>
          <svg viewBox="0 0 16 16" aria-hidden="true"><path d="M1 6c0-2 3-3 7-3s7 1 7 3v1h-3V5.5H4V7H1zM4 8h8l2 5H2z"/></svg>
          123 456 789
        </li>
        <li>
          <svg viewBox="0 0 16 16" aria-hidden="true"><path d="M1 3h14v1.5L8 9 1 4.5zM1 6.5 8 11l7-4.5V13H1z"/></svg>
          info@yourgmail.com
        </li>
        <li>
          <svg viewBox="0 0 16 16" aria-hidden="true"><circle cx="8" cy="8" r="7"/><path d="M4 5c2 0 3 1 2 3s1 3 1 5M10 2c0 2 2 2 3 4" stroke="#fff" stroke-width="1.2" fill="none"/></svg>
          www.yourwebsite.com
        </li>
      </ul>
    </div>
  </section>

  <section class="card card--back">
    <div class="wordmark">
      <span class="wordmark__square"></span>
      <span class="wordmark__name">Keldra Engineering Tandem</span>
    </div>
  </section>
</body>
</html>
```